Sunset Harbor Living Web Page

We need a web page design that has two intro pages - first being a 'home page', then a link to the second page that has the 'content tabs' and a 'call to action' (see below).

The business helps people that wish to retire to S.E.Asia (Thailand, Malaysia, Indonesia,The Philippines etc) - to enjoy the lifestyle and the remaining years of their lives. What attracts S.E.Asia to many people is the lower cost, the atmoshpere and beauty of the tropics and the vibrancy of the various countries.

People that are wishing to make the most of their retirement and are adventurous at a great bargain compared to the cost of their own countries will be interested.

We help them achieve this - visa, financials (tax, gov't payments etc), introduce them to the right people for property, clubs, retirement facilities, insurance and so forth.

Therefore we are providing an extremely wide ranging service and this site will provide broad but general information only - with a call to action to come and see us for more specific information and how we can help them specifically.

This site will be predominantly for travel and lifestyle, it will be linked with another financial services (financial planning) site later down the track.

The colour scheme is dark green and blue - as per the attached logo design. Photos and background just think lifestyle and S.E.Asia - beaches/mountains/water/recreational activities for retirees.

Target market is mostly those coming up to retirement to those that are already retired. But we also expect to have some interest with younger people that would like to find out more and plan for the future. So a broad age group but I would say mostly 40-70 yrs old.

On the first (Home) page we would like our company name 'Sunset Harbor Living', our logo (which will be on all pages) and a statement such as: “Imagine a retirement where your dreams are brought to life, and you have never felt more alive. Let us show you how”. Then a link to the second page.

We would like an uncluttered site. On the second (contents) page the tabs would be:

- Visa
- Property
- Financials
- Travel
- Insurance & Healthcare
- Medical Tourism
- Cost of living
- Weekly Blogs and articles
- Sunset Harbor Living story

We would also like a call to action on the second page - asking them to leave their contact details if they wish to learn more or sign up to our weekly newsletter/blog.

We are open to suggestions and your imaginations.

Thank you
Malcolm

Font styles to use
Serif
Script

Colors
0255a3
3377b5
00a990
9bcb3c
abd036
33b8a4
85abd2
cadf82
86cfc6

Requirements
Must have
• I have been asked by the web designer to receive a 'Web Font' so that we can 'get off of Zentrofy'. Hope that makes sense.

```html
<!DOCTYPE html>
<html lang="en">
<head>
<meta charset="utf-8">
<title>Sunset Harbor Living — Home</title>
<link rel="stylesheet" href="https://fonts.googleapis.com/css2?family=Cinzel:wght@700&family=Lato:wght@400;700;900&display=swap">
<style>
  :root {
    --brand-green: #0aa64a;
    --brand-blue: #0a93d6;
    --white: #ffffff;
    --sky-top: #7fa6c4;
    --sky-glow: #e9d6b4;
    --sea: #5f7486;
    --sand: #b9783f;
    --footer-bg: rgba(12, 14, 18, 0.9);
    --footer-rule: #8c8c8c;
    --footer-text: #e6e6e6;
  }
  * { box-sizing: border-box; margin: 0; padding: 0; }
  html, body { width: 1200px; height: 736px; overflow: hidden; background: #1b1b1b; }
  .page {
    position: relative;
    width: 1200px;
    height: 736px;
    overflow: hidden;
    font-family: "Lato", Arial, sans-serif;
  }
  .hero-photo {
    position: absolute;
    inset: 0;
    background: linear-gradient(180deg,
      var(--sky-top) 0%, var(--sky-glow) 45%, var(--sea) 62%, var(--sand) 100%);
  }
  .brand {
    position: absolute;
    top: 156px;
    left: 0;
    width: 1200px;
    text-align: center;
    color: var(--white);
  }
  .brand-name {
    font-weight: 900;
    font-size: 38px;
    letter-spacing: -0.5px;
    line-height: 1;
  }
  .brand-tagline {
    margin-top: 4px;
    font-weight: 900;
    font-size: 11.5px;
    letter-spacing: 1.5px;
    text-transform: uppercase;
  }
  .headline {
    position: absolute;
    top: 344px;
    left: 0;
    width: 1200px;
    text-align: center;
    font-family: "Cinzel", Georgia, serif;
    font-weight: 700;
    font-size: 33px;
    line-height: 41px;
    color: var(--brand-green);
    text-shadow: 0 0 2px #000, 2px 3px 5px rgba(0, 0, 0, 0.85);
  }
  .cta-button {
    position: absolute;
    left: 441px;
    top: 502px;
    width: 334px;
    height: 56px;
    display: flex;
    align-items: center;
    background: var(--brand-blue);
    border: 2px solid var(--white);
    border-radius: 5px;
    overflow: hidden;
    color: var(--white);
    text-decoration: none;
  }
  .cta-label {
    flex: 1;
    padding-left: 14px;
    font-weight: 700;
    font-size: 25px;
    letter-spacing: 0.3px;
  }
  .cta-arrow {
    width: 60px;
    height: 100%;
  }
  .site-footer {
    position: absolute;
    left: 0;
    top: 664px;
    width: 1200px;
    height: 72px;
    background: var(--footer-bg);
    border-top: 3px solid var(--footer-rule);
  }
  .newsletter {
    position: absolute;
    left: 157px;
    top: 16px;
    display: flex;
    align-items: center;
  }
  .newsletter-icon {
    width: 42px;
    height: 42px;
    position: relative;
    z-index: 1;
  }
  .newsletter-input {
    width: 214px;
    height: 30px;
    margin-left: -4px;
    background: var(--white);
    border: none;
    padding-left: 12px;
    font-family: "Lato", Arial, sans-serif;
    font-size: 12px;
    color: #333;
  }
  .newsletter-input::placeholder { color: #333; }
  .newsletter-submit {
    width: 30px;
    height: 30px;
    background: var(--brand-blue);
    border: none;
    border-radius: 0 3px 3px 0;
    display: flex;
    align-items: center;
    justify-content: center;
  }
  .contact {
    position: absolute;
    right: 158px;
    top: 14px;
    text-align: right;
    color: var(--footer-text);
    font-size: 13px;
  }
  .contact-lines {
    display: flex;
    justify-content: flex-end;
    gap: 18px;
  }
  .contact-item { display: flex; align-items: center; gap: 6px; }
  .copyright { margin-top: 8px; font-size: 13.5px; }
</style>
</head>
<body>
<main class="page">
  <div class="hero-photo" role="img" aria-label="Photo: retired couple relaxing in beach chairs, watching a tropical sunset over the sea"></div>

  <header class="brand">
    <div class="brand-name">Sunset Harbor Living</div>
    <div class="brand-tagline">Dream Lifestyle Specialists</div>
  </header>

  <h1 class="headline">
    Imagine A Retirement Where Your Dreams Are<br>
    Brought To Life,<br>
    &amp; You Have Never Felt More Alive
  </h1>

  <a class="cta-button" href="#contents">
    <span class="cta-label">Let Us Show You How</span>
    <svg class="cta-arrow" viewBox="0 0 60 56" aria-hidden="true">
      <path d="M30 0 H60 V56 H30 A28 28 0 0 1 30 0 Z" fill="var(--brand-green)" stroke="#fff" stroke-width="2"/>
      <path d="M25 18 L34 28 L25 38 M33 18 L42 28 L33 38" fill="none" stroke="#fff" stroke-width="1.8" stroke-linecap="round" stroke-linejoin="round"/>
    </svg>
  </a>

  <footer class="site-footer">
    <form class="newsletter">
      <svg class="newsletter-icon" viewBox="0 0 42 42" aria-hidden="true">
        <circle cx="21" cy="21" r="20" fill="#111" stroke="#fff" stroke-width="2"/>
        <path d="M9 22 L33 13 L25 30 L21 24 Z" fill="#fff"/>
        <path d="M21 24 L33 13" stroke="#111" stroke-width="1.5"/>
      </svg>
      <input class="newsletter-input" type="email" placeholder="Enter Your Email Address">
      <button class="newsletter-submit" type="submit" aria-label="Subscribe">
        <svg width="10" height="12" viewBox="0 0 10 12" aria-hidden="true"><path d="M2 1 L7 6 L2 11" fill="none" stroke="#fff" stroke-width="2"/></svg>
      </button>
    </form>

    <div class="contact">
      <div class="contact-lines">
        <span class="contact-item">
          <svg width="12" height="12" viewBox="0 0 24 24" aria-hidden="true"><path d="M6.6 10.8a15.1 15.1 0 0 0 6.6 6.6l2.2-2.2a1 1 0 0 1 1-.25 11.4 11.4 0 0 0 3.6.57 1 1 0 0 1 1 1V20a1 1 0 0 1-1 1A17 17 0 0 1 3 4a1 1 0 0 1 1-1h3.5a1 1 0 0 1 1 1c0 1.25.2 2.45.57 3.57a1 1 0 0 1-.25 1Z" fill="var(--brand-green)"/></svg>
          (123) 456-7890
        </span>
        <span class="contact-item">
          <svg width="15" height="11" viewBox="0 0 15 11" aria-hidden="true"><rect width="15" height="11" fill="var(--brand-green)"/><path d="M0 0 L7.5 6 L15 0" fill="none" stroke="#111" stroke-width="1.2"/></svg>
          info@sunsetharborliving.com
        </span>
      </div>
      <div class="copyright">Copyright © 2016 Sunset Harbor Living&nbsp; | &nbsp;All Rights Reserved.</div>
    </div>
  </footer>
</main>
</body>
</html>
```